Stationary Set Rebrand for Brennick

We are a Canadian Distribution and Service Company that was established in 1969. Over the past 5 decades we have expanded our business and have warehouses across Canada. We specialize in adhesive tapes, adhesives, films, safety, warehouse, shipping, janitorial and packaging supplies.

We have updated our logo design and would like a new corporate branding identity that includes a new fresh Stationary Set (Business Cards, Letterhead, Letterhead MS Word, Envelope, Presentation Folders, Email Signatures, Notepad Covers, etc.)

Target Market(s)

Industrial Business Sector

Font styles to use
Sans Serif

Colors
0054AA
0677BA
7BADD7
CADEEF
E8F1F8
0094D4
00A9DD
6FCCEA
C7EBF8
E9F6FB
00AB8E
00BBA5
67D7C9
C6EFE9
E9F9F6
EB3D1F
EC4F4E
F09395
F8D3D4
FCEDEE

Requirements
Should not have
• Colors not too light, darker colours preferred

```html
<!DOCTYPE html>
<html lang="en">
<head>
<meta charset="utf-8">
<title>Brennick Business Card</title>
<link rel="stylesheet" href="https://fonts.googleapis.com/css2?family=Nunito:wght@400;600;800&display=swap">
<style>
  :root {
    --bg: #9b9b9b;
    --card: #1c1c1d;
    --card-back: #141415;
    --red: #d9262c;
    --white: #f4f4f4;
    --muted: #e6e6e6;
  }
  * { margin: 0; padding: 0; box-sizing: border-box; }
  html, body { width: 1200px; height: 1083px; overflow: hidden; }
  body {
    background: var(--bg);
    font-family: "Nunito", sans-serif;
    position: relative;
  }
  .card {
    position: absolute;
    left: 290px;
    width: 620px;
    height: 354px;
    border-bottom: 3px solid var(--red);
    box-shadow: 0 18px 40px rgba(0,0,0,0.35);
  }
  .card-front { top: 150px; background: var(--card); }
  .card-back { top: 580px; background: var(--card-back); overflow: hidden; }

  .brand-name {
    position: absolute;
    right: 40px;
    top: 48px;
    font-size: 44px;
    font-weight: 800;
    color: var(--white);
    letter-spacing: 0.5px;
  }
  .holder { position: absolute; left: 40px; top: 112px; }
  .holder-name {
    font-size: 22px;
    font-weight: 600;
    color: var(--red);
    text-transform: uppercase;
    letter-spacing: 0.5px;
  }
  .holder-title { font-size: 15px; color: var(--muted); margin-top: 2px; }
  .divider {
    position: absolute;
    left: 30px;
    right: 30px;
    top: 176px;
    height: 1.5px;
    background: var(--red);
  }
  .contacts {
    position: absolute;
    left: 40px;
    top: 192px;
    list-style: none;
    font-size: 14px;
    color: var(--muted);
  }
  .contacts li { display: flex; align-items: center; gap: 12px; height: 24px; }
  .contacts svg { width: 14px; height: 14px; fill: var(--red); flex: none; }
  .address {
    position: absolute;
    right: 40px;
    bottom: 30px;
    text-align: right;
    font-size: 15px;
    line-height: 1.45;
    color: var(--muted);
  }
  .leaf-pattern {
    position: absolute;
    inset: 0;
    background: linear-gradient(110deg, #4a4a4c 0%, #2a2a2b 40%, #141415 70%, #101011 100%);
  }
</style>
</head>
<body>
  <section class="card card-front">
    <div class="brand-name">Brennick</div>
    <div class="holder">
      <h1 class="holder-name">Daniel Mercer</h1>
      <p class="holder-title">Development Manager Officer</p>
    </div>
    <div class="divider"></div>
    <ul class="contacts">
      <li>
        <svg viewBox="0 0 24 24" aria-hidden="true"><path d="M6.6 10.8a15.1 15.1 0 0 0 6.6 6.6l2.2-2.2c.3-.3.7-.4 1-.2 1.1.4 2.3.6 3.6.6.6 0 1 .4 1 1V20c0 .6-.4 1-1 1A17 17 0 0 1 3 4c0-.6.4-1 1-1h3.5c.6 0 1 .4 1 1 0 1.3.2 2.5.6 3.6.1.3 0 .7-.2 1z"/></svg>
        789-555-0142
      </li>
      <li>
        <svg viewBox="0 0 24 24" aria-hidden="true"><path d="M2 5h20v14H2z M2 5l10 8 10-8" /></svg>
        daniel.mercer@brennicksupply.com
      </li>
      <li>
        <svg viewBox="0 0 24 24" aria-hidden="true"><path d="M12 2a10 10 0 1 0 0 20 10 10 0 0 0 0-20zm6.9 9h-3a15 15 0 0 0-1.3-5.6A8 8 0 0 1 18.9 11zM12 4c.9 1.2 1.8 3.6 1.9 7h-3.8c.1-3.4 1-5.8 1.9-7zM9.4 5.4A15 15 0 0 0 8.1 11h-3a8 8 0 0 1 4.3-5.6zM5.1 13h3a15 15 0 0 0 1.3 5.6A8 8 0 0 1 5.1 13zM12 20c-.9-1.2-1.8-3.6-1.9-7h3.8c-.1 3.4-1 5.8-1.9 7zm2.6-1.4a15 15 0 0 0 1.3-5.6h3a8 8 0 0 1-4.3 5.6z"/></svg>
        brennicksupply.com
      </li>
    </ul>
    <address class="address" style="font-style:normal">
      412 Harbour Road<br>
      Suite 210, Toronto<br>
      ON M5V 2K8
    </address>
  </section>

  <section class="card card-back">
    <div class="leaf-pattern" role="img" aria-label="Repeating pattern of maple leaves fading from grey to black across the card"></div>
  </section>
</body>
</html>
```